Membership Based Medical Practice Website

We need a functioning website for a new Membership based medical practice. There will be an enrollment fee and a monthly fee. We would like to see designs that are modern, simple. Should use neutral light colors. Examples of sites we like are www.kellanmoorclinic.com and https://fernholtcare.com/ We also have a link that when "Join Now" is clicked it will go to the signup website.

Target Market(s)

Gay Men, local population, Age group 20 to 60's.

Industry/Entity Type

Medical

Coding

Coded - Design and coding required

Number of Pages Required

5+ page

Font styles to use
Sans Serif

Colors
ffffff
cee9f5
ecf7fb
cfeae6
edf8f6
aaaaaa
e9e9e9
dbdbdb
fff3d1

Requirements
Must have
• Logo and header on every page. Clean, simple design, clear content, mobile compatible.
• Must use Wordpress
Nice to have
• Ideas should come from kellanmoorclinic.com
• Easy to read
Should not have
• Generic patient pictures, bold colors.
• Should not copy from above websites.

```html
<!DOCTYPE html>
<html lang="en">
<head>
<meta charset="utf-8">
<title>Larkmoor Infectious Disease Specialists</title>
<link rel="stylesheet" href="https://fonts.googleapis.com/css2?family=Montserrat:wght@400;500;600;700&family=Josefin+Sans:wght@300;400&display=swap">
<style>
:root{
  --cream:#fff3d1;
  --sky:#cee9f5;
  --sky-pale:#ecf7fb;
  --hex:#a9dcf5;
  --ink:#2b2b2b;
  --text:#555555;
  --muted:#6b6b6b;
  --white:#ffffff;
  --night:#2a2b2d;
}
*{margin:0;padding:0;box-sizing:border-box}
html,body{width:1200px;height:3704px;overflow:hidden}
body{position:relative;background:var(--white);font-family:"Montserrat",sans-serif;color:var(--ink)}
.abs{position:absolute}
.topbar{left:0;top:0;width:1200px;height:62px;background:var(--cream)}
.topbar .hours{left:95px;top:21px;font-size:15px;font-weight:500}
.social{display:flex;gap:14px}
.social span{width:22px;height:22px;border-radius:4px;background:#4a4a4a;display:block}
.topbar .social{right:95px;top:20px}
.header{left:0;top:62px;width:1200px;height:196px;background:var(--white)}
.brand{text-align:center}
.brand .dot{width:70px;height:70px;border-radius:50%;border:2px solid #e2c27a;margin:0 auto 14px}
.brand .name{font-size:15px;letter-spacing:14px;color:#4a4a4a}
.brand .sub{font-size:12px;letter-spacing:.5px;color:#4a4a4a;margin-top:4px}
.header .brand{left:98px;top:18px;width:235px}
.join{left:962px;top:30px;width:148px;height:48px;border-radius:24px;background:var(--sky);font-size:18px;display:flex;align-items:center;justify-content:center;color:var(--ink)}
.nav{display:flex;gap:36px;font-size:17px;color:#555}
.header .nav{right:95px;top:124px}
.hero{left:0;top:258px;width:1200px;height:582px;background:linear-gradient(180deg,#8b8f91 0%,#b7a896 45%,#c49a62 70%,#5a4a36 100%)}
.hero h1{left:0;top:190px;width:1200px;text-align:center;color:var(--white);font-size:47px;font-weight:700;line-height:1.3}
.btn-pale{background:var(--sky);border-radius:30px;display:flex;align-items:center;justify-content:center;font-size:20px;color:var(--ink)}
.hero .btn-pale{left:526px;top:352px;width:184px;height:60px}
.intro{left:0;width:1200px;text-align:center;color:var(--muted)}
.intro.lead{top:905px;font-size:23px}
.intro.sub{top:957px;font-size:21px;color:#444}
.spec{width:300px;text-align:center}
.spec .circle{width:212px;height:212px;border-radius:50%;background:var(--cream);margin:0 auto;display:flex;align-items:center;justify-content:center}
.spec p{font-family:"Josefin Sans",sans-serif;font-size:22px;color:#444;margin-top:30px;line-height:1.3}
.more{left:508px;top:1847px;width:180px;height:60px;font-size:19px}
.perks{left:0;top:1993px;width:1200px;height:664px;background:var(--cream)}
.perks h2{left:0;top:52px;width:1200px;text-align:center;font-size:33px;font-weight:500;color:#444}
.perks .tag{left:0;top:114px;width:1200px;text-align:center;font-size:23px;color:#555}
.arrow{width:28px;height:28px;border-radius:50%;background:#4a4a4a;display:flex;align-items:center;justify-content:center}
.perk{width:230px;text-align:center;font-family:"Josefin Sans",sans-serif}
.perk .hex{width:200px;height:176px;margin:0 auto;background:var(--hex);clip-path:polygon(25% 0,75% 0,100% 50%,75% 100%,25% 100%,0 50%);display:flex;align-items:center;justify-content:center}
.perk h3{font-weight:400;font-size:20px;color:#444;margin-top:24px;line-height:1.3}
.perk p{font-size:15px;color:#333;margin:24px auto 0;width:180px;line-height:1.35}
.pricing{left:0;top:2657px;width:685px;height:553px;background:linear-gradient(180deg,#ffffff 0%,var(--sky-pale) 45%,#cde8f4 100%)}
.pricing .copy{left:110px;top:38px;width:560px}
.pricing h4{font-weight:400;font-size:22px;color:#444;line-height:1.3}
.pricing .plan{margin-top:30px}
.pricing ul{list-style:none;margin-top:28px;font-family:"Josefin Sans",sans-serif;font-size:16px;color:#333}
.pricing li{display:flex;gap:16px;align-items:flex-start;line-height:1.9}
.pricing li i{flex:none;width:18px;height:18px;border-radius:50%;border:2px solid #999;margin-top:6px}
.pricing li.plain i{visibility:hidden}
.learn{margin-top:28px;width:272px;height:58px;border-radius:29px;background:#111;color:var(--white);font-size:20px;display:flex;align-items:center;justify-content:center}
.photo-mug{left:685px;top:2657px;width:515px;height:553px;background:radial-gradient(circle at 70% 40%,#e9e5df 0%,#b8a9a0 30%,#8a4f46 60%,#3c3d3f 100%)}
.footer{left:0;top:3210px;width:1200px;height:494px;background:linear-gradient(180deg,#3a3b3d 0%,var(--night) 60%,#1e1f21 100%)}
.footer .brand{left:450px;top:62px;width:300px}
.footer .brand .dot{border-color:#d9d9d9;width:100px;height:100px}
.footer .brand .name,.footer .brand .sub{color:var(--white)}
.footer .brand .name{font-size:22px;letter-spacing:20px}
.footer .brand .sub{font-size:17px}
.footer .nav{left:0;width:1200px;justify-content:center;top:312px;color:var(--white);font-size:18px;gap:28px}
.footer .copy{left:100px;top:426px;font-size:16px;color:var(--white)}
.footer .social{right:90px;top:423px}
.footer .social span{background:var(--white);width:25px;height:25px}
</style>
</head>
<body>
<div class="abs topbar">
  <div class="abs hours">Office hours by appointment only</div>
  <div class="abs social"><span></span><span></span><span></span><span></span></div>
</div>

<header class="abs header">
  <div class="abs brand"><div class="dot"></div><div class="name">LARKMOOR</div><div class="sub">INFECTIOUS DISEASE SPECIALISTS</div></div>
  <div class="abs join">Join us</div>
  <nav class="abs nav"><span>Home</span><span>Specialties</span><span>Pricing</span><span>About Us</span><span>Faq</span><span>Blog</span></nav>
</header>

<section class="abs hero" role="img" aria-label="Photo of four friends arm in arm on a hillside at sunset">
  <h1 class="abs">Specialty medicine with Commitment,<br>Compassion and Care</h1>
  <div class="abs btn-pale">View More</div>
</section>

<p class="abs intro lead">We offer comprehensive treatment of a wide variety of infectious diseases</p>
<p class="abs intro sub">Our expertise is in the following area</p>

<div class="abs spec" style="left:115px;top:1072px"><div class="circle" role="img" aria-label="Virus icon"></div><p>HIV/PrEP</p></div>
<div class="abs spec" style="left:452px;top:1072px"><div class="circle" role="img" aria-label="Liver icon"></div><p>Chronic Hepatitis</p></div>
<div class="abs spec" style="left:790px;top:1072px"><div class="circle" role="img" aria-label="Gender symbols icon"></div><p>Sexually transmitted<br>infections</p></div>
<div class="abs spec" style="left:115px;top:1452px"><div class="circle">
  <svg width="60" height="150" viewBox="0 0 60 150" fill="none" stroke="#333" stroke-width="3"><line x1="15" y1="5" x2="45" y2="5"/><line x1="30" y1="5" x2="30" y2="28"/><line x1="14" y1="28" x2="46" y2="28"/><rect x="20" y="28" width="20" height="80"/><line x1="20" y1="50" x2="30" y2="50"/><line x1="20" y1="70" x2="30" y2="70"/><line x1="20" y1="90" x2="30" y2="90"/><path d="M22 108 L30 120 L38 108"/><line x1="30" y1="120" x2="30" y2="145"/></svg>
</div><p>Pre-travel vaccinations<br>and counselling</p></div>
<div class="abs spec" style="left:452px;top:1452px"><div class="circle" role="img" aria-label="Medical device icon"></div><p>Infections associated<br>with medical devices</p></div>
<div class="abs spec" style="left:790px;top:1452px"><div class="circle" role="img" aria-label="Knee joint icon"></div><p>Bone and Joint<br>infections</p></div>

<div class="abs btn-pale more">View More</div>

<section class="abs perks">
  <h2 class="abs">Less wait, more personal</h2>
  <p class="abs tag">We are not your traditional doctor’s office</p>
  <div class="abs arrow" style="left:40px;top:318px"><svg width="12" height="12" viewBox="0 0 12 12"><path d="M8 1 L3 6 L8 11" stroke="#fff" stroke-width="2" fill="none"/></svg></div>
  <div class="abs arrow" style="left:1132px;top:318px"><svg width="12" height="12" viewBox="0 0 12 12"><path d="M4 1 L9 6 L4 11" stroke="#fff" stroke-width="2" fill="none"/></svg></div>

  <div class="abs perk" style="left:108px;top:218px">
    <div class="hex"><svg width="80" height="80" viewBox="0 0 80 80" fill="none" stroke="#fff" stroke-width="3"><circle cx="40" cy="40" r="34"/><text x="40" y="54" text-anchor="middle" font-size="40" fill="#fff" stroke="none" font-family="Montserrat,sans-serif">$</text></svg></div>
    <h3>Straight forward<br>Pricing</h3>
    <p>We charge all our patients the same low rate - no surprises.</p>
  </div>
  <div class="abs perk" style="left:372px;top:218px">
    <div class="hex"><svg width="90" height="80" viewBox="0 0 90 80" fill="none" stroke="#fff" stroke-width="3"><rect x="5" y="12" width="80" height="62" rx="4"/><line x1="5" y1="28" x2="85" y2="28"/><line x1="25" y1="4" x2="25" y2="18"/><line x1="65" y1="4" x2="65" y2="18"/><circle cx="22" cy="42" r="4"/><circle cx="38" cy="42" r="4"/><circle cx="54" cy="42" r="4"/><circle cx="70" cy="42" r="4"/><circle cx="22" cy="58" r="4"/><circle cx="38" cy="58" r="4"/><path d="M56 58 l6 6 l12 -12"/></svg></div>
    <h3>Available when<br>you are</h3>
    <p>New patient appointments are available within 1 week.</p>
  </div>
  <div class="abs perk" style="left:615px;top:218px">
    <div class="hex"><svg width="90" height="70" viewBox="0 0 90 70" fill="none" stroke="#fff" stroke-width="3"><path d="M45 12 C35 4 15 4 5 8 V64 C15 60 35 60 45 68 C55 60 75 60 85 64 V8 C75 4 55 4 45 12 Z"/><line x1="45" y1="12" x2="45" y2="68"/></svg></div>
    <h3>Hassle-free<br>booking</h3>
    <p>Schedule your appointment online at your convenience - no need to call during business hours.</p>
  </div>
  <div class="abs perk" style="left:862px;top:218px">
    <div class="hex"><svg width="80" height="80" viewBox="0 0 80 80" fill="none" stroke="#fff" stroke-width="3"><path d="M40 58 C20 44 18 30 28 26 C34 24 38 28 40 32 C42 28 46 24 52 26 C62 30 60 44 40 58 Z"/><circle cx="40" cy="40" r="34"/></svg></div>
    <h3>Devoted<br>care</h3>
    <p>We schedule enough time at each visit to make sure all of your questions are answered.</p>
  </div>
</section>

<section class="abs pricing">
  <div class="abs copy">
    <h4>Our pricing is simple, transparent<br>and affordable.</h4>
    <h4 class="plan">Membership Plan $80/mo, plus a one-time<br>$99 enrollment fee.</h4>
    <ul>
      <li class="plain"><i></i>Includes all appointments, no co-pay</li>
      <li><i></i>Relaxed, unrushed visits</li>
      <li><i></i>Direct communication with your doctor via phone, email, video chat 24/7</li>
      <li><i></i>Convenient online scheduling (no need to call during business hours)</li>
      <li><i></i>Wholesale price for labs and medications</li>
    </ul>
    <div class="learn">Learn more about us</div>
  </div>
</section>
<div class="abs photo-mug" role="img" aria-label="Photo of a hand holding an enamel camping mug"></div>

<footer class="abs footer">
  <div class="abs brand"><div class="dot"></div><div class="name">LARKMOOR</div><div class="sub">INFECTIOUS DISEASE SPECIALISTS</div></div>
  <nav class="abs nav"><span>Home</span><span>Specialties</span><span>Pricing</span><span>About Us</span><span>Faq</span><span>Blog</span></nav>
  <div class="abs copy">2019 © Copyrights Larkmoor Infectious Disease Specialists</div>
  <div class="abs social"><span></span><span></span><span></span><span></span></div>
</footer>
</body>
</html>
```